Calloway needs a modernized design

We would like a modern update (that can be responsive) to our existing website. Attached are the two existing pages we would like new concepts of - our home page and a page about one of our locations.

Calloway is provides executive offices and virtual office services. Startups, law firms, and financial services are our primary clients. We would like a professional, clean design, leaning towards minimalist. We intend to greatly reduce/eliminate the long paragraphs of text.

Requirements
Must have
• A design that can be responsive
Nice to have
• Large image(s) on home page that rotate.

```html
<!DOCTYPE html>
<html lang="en">
<head>
<meta charset="utf-8">
<title>Calloway Business Centers</title>
<link rel="stylesheet" href="https://fonts.googleapis.com/css2?family=Cinzel:wght@400;700&family=Open+Sans:wght@400;600;700&display=swap">
<style>
:root{
  --navy:#1b3361;
  --blue:#24508f;
  --blue-light:#3a6bb0;
  --orange:#f39224;
  --orange-dark:#e07c10;
  --ink:#2a2f3a;
  --grey:#6b6f78;
  --pale:#eef0f3;
  --white:#ffffff;
}
*{margin:0;padding:0;box-sizing:border-box}
html,body{width:1200px;height:2768px;overflow:hidden}
body{font-family:"Open Sans",Arial,sans-serif;color:var(--ink);background:var(--white);position:relative}
.serif{font-family:"Cinzel",Georgia,serif}
section,header,footer{position:absolute;left:0;width:1200px}

/* header */
.site-header{top:0;height:100px;background:var(--white)}
.brand{position:absolute;left:24px;top:18px;display:flex;align-items:center;gap:12px}
.brand-dot{width:52px;height:52px;border-radius:50%;background:var(--blue)}
.brand-name{font-family:"Cinzel",Georgia,serif;font-weight:700;font-size:26px;color:var(--navy);line-height:1}
.topbar{position:absolute;right:24px;top:12px;display:flex;align-items:center;gap:8px}
.topbar .soc{width:26px;height:26px;border-radius:50%;background:var(--blue)}
.topbar .soc.alt{background:var(--orange)}
.phone-btn{margin-left:8px;background:var(--orange);color:var(--white);font-weight:700;font-size:14px;padding:5px 14px;border-radius:3px;display:flex;align-items:center;gap:6px}
.main-nav{position:absolute;right:24px;top:58px;display:flex;align-items:center;gap:34px;font-family:"Cinzel",Georgia,serif;font-weight:700;font-size:15px;color:var(--navy)}

/* hero */
.hero{top:100px;height:420px;background:linear-gradient(180deg,#5e6c7e 0%,#8a95a3 35%,#b9bfc6 70%,#d6d8db 100%)}
.hero-arrow{position:absolute;top:185px;width:34px;height:50px;background:rgba(20,30,50,.7);display:flex;align-items:center;justify-content:center}
.hero-badge{position:absolute;left:890px;top:90px;width:240px;height:240px;border-radius:50%;background:rgba(20,40,80,.82);border:3px solid rgba(255,255,255,.8);display:flex;flex-direction:column;align-items:center;justify-content:center;text-align:center;color:var(--white);padding:0 26px}
.hero-badge .dot{width:40px;height:40px;border-radius:50%;background:var(--white);margin-bottom:14px}
.hero-badge p{font-weight:600;font-size:19px;line-height:1.3}

/* welcome */
.welcome{top:520px;height:480px;text-align:center}
.welcome h1{margin-top:70px;font-family:"Cinzel",Georgia,serif;font-weight:700;font-size:36px;color:var(--navy);letter-spacing:1px}
.welcome .lead{width:860px;margin:26px auto 0;font-weight:700;color:var(--orange);font-size:17px;line-height:1.5}
.welcome .body{width:980px;margin:18px auto 0;color:var(--grey);font-size:14px;line-height:1.7}
.btn{display:inline-flex;align-items:center;gap:6px;background:var(--orange);color:var(--white);font-weight:700;font-size:13px;padding:7px 18px;border-radius:3px}
.btn.blue{background:var(--blue)}
.welcome .btn{margin-top:30px}

/* offers */
.offers{top:1000px;height:410px}
.offer{position:absolute;top:0;width:600px;height:410px;padding-top:70px;text-align:center}
.offer.exec{left:0;background:linear-gradient(180deg,#2f5c9c 0%,var(--blue) 45%,var(--navy) 100%)}
.offer.virtual{left:600px;background:linear-gradient(180deg,#f7a443 0%,var(--orange) 45%,var(--orange-dark) 100%)}
.offer-icon{width:110px;height:110px;border-radius:50%;margin:0 auto;border:5px solid var(--white);display:flex;align-items:center;justify-content:center}
.exec .offer-icon{background:var(--orange)}
.virtual .offer-icon{background:var(--blue)}
.offer h2{margin-top:18px;font-family:"Cinzel",Georgia,serif;font-weight:400;font-size:30px}
.exec h2{color:var(--orange)}
.virtual h2{color:var(--navy)}
.offer ul{list-style:none;width:430px;margin:18px auto 0;display:grid;grid-template-columns:1fr 1fr;row-gap:9px;text-align:left;font-size:13px;color:var(--white)}
.offer li{display:flex;align-items:center;gap:7px}
.offer .btn{margin-top:20px}
.offer.exec .btn{margin-left:250px}
.offer.virtual .btn{margin-left:250px}
.offers-hub{position:absolute;left:560px;top:26px;width:80px;height:80px;border-radius:50%;background:var(--white);border:6px solid var(--blue);box-shadow:0 0 0 5px rgba(255,255,255,.6)}

/* community & services */
.info{top:1410px;height:740px}
.community{position:absolute;left:0;top:0;width:600px;height:740px;background:var(--pale);padding:44px 46px 0}
.services{position:absolute;left:600px;top:0;width:600px;height:740px;padding:44px 46px 0}
.info h2{font-family:"Cinzel",Georgia,serif;font-weight:700;font-size:32px;color:var(--navy)}
.community-photo{margin-top:28px;width:508px;height:260px;background:linear-gradient(135deg,#c99a6e 0%,#e0b58a 40%,#a8744d 100%)}
.community p{margin-top:22px;font-size:13px;line-height:1.75;color:var(--grey)}
.community .btn{margin-top:20px}
.service{display:flex;gap:20px;margin-top:40px}
.service:first-of-type{margin-top:36px}
.service-icon{flex:none;width:84px;height:84px;border-radius:50%;background:var(--ink);border:4px solid #c9ccd2;display:flex;align-items:center;justify-content:center}
.service h3{font-weight:700;font-size:18px;color:var(--orange)}
.service p{margin-top:6px;font-size:13px;line-height:1.6;color:var(--grey)}
.service .more{margin-top:8px;font-size:13px;font-weight:700;color:var(--navy)}

/* partners */
.partners{top:2150px;height:290px;text-align:center}
.partners h2{margin-top:42px;font-family:"Cinzel",Georgia,serif;font-weight:700;font-size:32px;color:var(--navy)}
.partners .mark{width:24px;height:24px;border-radius:50%;background:var(--blue);margin:10px auto 0}
.partner-row{position:absolute;left:60px;top:130px;width:1080px;display:flex;justify-content:space-between}
.partner{width:160px;height:90px;border:1px solid #d9dce1;display:flex;align-items:center;justify-content:center}
.partner span{display:block;width:110px;height:30px;border-radius:4px;background:#c5c9d0}
.partner-arrow{position:absolute;top:160px;width:30px;height:30px;display:flex;align-items:center;justify-content:center}

/* footer */
.site-footer{top:2440px;height:300px;background:linear-gradient(180deg,var(--blue) 0%,var(--navy) 100%);color:var(--white)}
.footer-hub{position:absolute;left:568px;top:-32px;width:64px;height:64px;border-radius:50%;background:var(--white);border:5px solid var(--blue)}
.footer-cols{position:absolute;left:40px;top:60px;width:1120px;display:grid;grid-template-columns:240px 300px 330px 200px;column-gap:16px}
.footer-cols h4{font-family:"Cinzel",Georgia,serif;font-weight:700;font-size:17px;letter-spacing:1px;padding-bottom:10px;border-bottom:1px solid rgba(255,255,255,.3);margin-bottom:14px}
.footer-cols ul{list-style:none;font-size:13px;line-height:2}
.footer-cols li::before{content:"› ";color:var(--orange)}
.contact-line{font-size:12.5px;line-height:1.6;margin-bottom:10px;display:flex;gap:8px}
.contact-line b{font-weight:700}
.form-field{height:30px;background:var(--white);border-radius:2px;margin-bottom:8px;font-size:12px;color:#9aa0a8;padding:6px 10px}
.form-field.tall{height:54px}
.submit{display:inline-block;background:var(--blue-light);border:1px solid rgba(255,255,255,.5);color:var(--white);font-weight:700;font-size:13px;padding:5px 24px;border-radius:2px}
.follow li{display:flex;align-items:center;gap:10px;font-weight:700;margin-bottom:6px}
.follow li::before{content:none}
.follow .ic{width:26px;height:26px;border-radius:50%;background:var(--orange)}
.copyright{top:2740px;height:28px;background:var(--orange);color:var(--white);font-size:12px;text-align:center;line-height:28px}
</style>
</head>
<body>

<header class="site-header">
  <div class="brand"><span class="brand-dot"></span><span class="brand-name">Calloway Business Centers</span></div>
  <div class="topbar">
    <span class="soc alt"></span><span class="soc"></span><span class="soc"></span><span class="soc alt"></span>
    <span class="phone-btn">
      <svg width="14" height="14" viewBox="0 0 24 24"><path fill="#fff" d="M6.6 10.8a15 15 0 0 0 6.6 6.6l2.2-2.2c.3-.3.7-.4 1-.2 1.1.4 2.3.6 3.6.6.6 0 1 .4 1 1V20c0 .6-.4 1-1 1A17 17 0 0 1 3 4c0-.6.4-1 1-1h3.5c.6 0 1 .4 1 1 0 1.3.2 2.5.6 3.6.1.3 0 .7-.2 1z"/></svg>
      +214.555.0147
    </span>
  </div>
  <nav class="main-nav">
    <svg width="22" height="20" viewBox="0 0 24 22"><path fill="#1b3361" d="M12 1 1 11h3v10h6v-6h4v6h6V11h3z"/></svg>
    <span>Properties</span><span>Virtual Tours &amp; Videos</span><span>Photos</span><span>Broker Referrals</span>
  </nav>
</header>

<section class="hero" role="img" aria-label="Photo of a long executive boardroom table with black chairs and glass walls">
  <span class="hero-arrow" style="left:0"><svg width="12" height="18" viewBox="0 0 12 18"><path d="M10 2 3 9l7 7" stroke="#fff" stroke-width="3" fill="none"/></svg></span>
  <span class="hero-arrow" style="right:0"><svg width="12" height="18" viewBox="0 0 12 18"><path d="m2 2 7 7-7 7" stroke="#fff" stroke-width="3" fill="none"/></svg></span>
  <div class="hero-badge"><span class="dot"></span><p>We Provide Executive Offices And Virtual Office Services</p></div>
</section>

<section class="welcome">
  <h1>WELCOME TO CALLOWAY BUSINESS CENTERS</h1>
  <p class="lead">Come See Why Smarter Companies are Choosing Calloway Business Centers' Dallas, Ft. Worth and Houston Executive Office Suites, Virtual Offices, Meeting Rooms and Video Conferencing.</p>
  <p class="body">Whether you need Dallas office space, a Ft. Worth executive suite or a Houston private office, or maybe you only need a place to drop in and use an on-demand office or meeting room from time to time, you can rely on our local business phone numbers, phone answering or business addresses through one of our virtual office solutions.</p>
  <span class="btn">Read More <svg width="10" height="10" viewBox="0 0 10 10"><path d="m3 1 4 4-4 4" stroke="#fff" stroke-width="2" fill="none"/></svg></span>
</section>

<section class="offers">
  <div class="offer exec">
    <div class="offer-icon"><svg width="54" height="54" viewBox="0 0 54 54"><rect x="8" y="26" width="38" height="4" fill="#fff"/><rect x="12" y="30" width="4" height="16" fill="#fff"/><rect x="38" y="30" width="4" height="16" fill="#fff"/><rect x="20" y="8" width="14" height="16" rx="2" fill="#fff"/></svg></div>
    <h2>Executive Offices</h2>
    <ul>
      <li><svg width="12" height="12" viewBox="0 0 12 12"><path d="m1 6 3 3 7-7" stroke="#f39224" stroke-width="2" fill="none"/></svg>Full Service Office</li>
      <li><svg width="12" height="12" viewBox="0 0 12 12"><path d="m1 6 3 3 7-7" stroke="#f39224" stroke-width="2" fill="none"/></svg>Flexible Contracts from $395</li>
      <li><svg width="12" height="12" viewBox="0 0 12 12"><path d="m1 6 3 3 7-7" stroke="#f39224" stroke-width="2" fill="none"/></svg>Disaster Recovery</li>
      <li><svg width="12" height="12" viewBox="0 0 12 12"><path d="m1 6 3 3 7-7" stroke="#f39224" stroke-width="2" fill="none"/></svg>Corporate or Satellite Offices</li>
      <li><svg width="12" height="12" viewBox="0 0 12 12"><path d="m1 6 3 3 7-7" stroke="#f39224" stroke-width="2" fill="none"/></svg>All-Inclusive Pricing!</li>
    </ul>
    <span class="btn">Read More <svg width="10" height="10" viewBox="0 0 10 10"><path d="m3 1 4 4-4 4" stroke="#fff" stroke-width="2" fill="none"/></svg></span>
  </div>
  <div class="offer virtual">
    <div class="offer-icon"><svg width="54" height="54" viewBox="0 0 54 54"><circle cx="27" cy="18" r="9" fill="#fff"/><path d="M10 46c0-10 8-16 17-16s17 6 17 16z" fill="#fff"/></svg></div>
    <h2>Virtual Office</h2>
    <ul>
      <li><svg width="12" height="12" viewBox="0 0 12 12"><path d="m1 6 3 3 7-7" stroke="#1b3361" stroke-width="2" fill="none"/></svg>Mailing Address Service</li>
      <li><svg width="12" height="12" viewBox="0 0 12 12"><path d="m1 6 3 3 7-7" stroke="#1b3361" stroke-width="2" fill="none"/></svg>Flexible Contracts</li>
      <li><svg width="12" height="12" viewBox="0 0 12 12"><path d="m1 6 3 3 7-7" stroke="#1b3361" stroke-width="2" fill="none"/></svg>Local Phone &amp; Mail Service</li>
      <li><svg width="12" height="12" viewBox="0 0 12 12"><path d="m1 6 3 3 7-7" stroke="#1b3361" stroke-width="2" fill="none"/></svg>All-Inclusive Pricing!</li>
      <li><svg width="12" height="12" viewBox="0 0 12 12"><path d="m1 6 3 3 7-7" stroke="#1b3361" stroke-width="2" fill="none"/></svg>Corporate or Satellite Offices</li>
    </ul>
    <span class="btn blue">Read More <svg width="10" height="10" viewBox="0 0 10 10"><path d="m3 1 4 4-4 4" stroke="#fff" stroke-width="2" fill="none"/></svg></span>
  </div>
  <span class="offers-hub"></span>
</section>

<section class="info">
  <div class="community">
    <h2>COMMUNITY</h2>
    <div class="community-photo" role="img" aria-label="Photo of many hands stacked together in a team huddle"></div>
    <p>Our centers are more than a desk and a door. Every member joins a community of founders, attorneys and advisors who share ideas, referrals and coffee. Regular networking lunches, workshops and member events help you meet the people who can grow your business, while our friendly local staff keep each day running smoothly so you can focus on clients and the work that matters most to you.</p>
    <span class="btn">Read More <svg width="10" height="10" viewBox="0 0 10 10"><path d="m3 1 4 4-4 4" stroke="#fff" stroke-width="2" fill="none"/></svg></span>
  </div>
  <div class="services">
    <h2>OTHER SERVICES</h2>
    <div class="service">
      <span class="service-icon"><svg width="38" height="38" viewBox="0 0 38 38"><rect x="5" y="14" width="28" height="4" fill="#fff"/><circle cx="10" cy="9" r="3" fill="#fff"/><circle cx="19" cy="9" r="3" fill="#fff"/><circle cx="28" cy="9" r="3" fill="#fff"/><rect x="8" y="18" width="3" height="12" fill="#fff"/><rect x="27" y="18" width="3" height="12" fill="#fff"/></svg></span>
      <div><h3>On-demand Meeting Rooms</h3><p>Book a polished boardroom by the hour or day, with screens, fast internet and coffee service ready when your guests arrive.</p><div class="more">Read More ›</div></div>
    </div>
    <div class="service">
      <span class="service-icon"><svg width="38" height="38" viewBox="0 0 38 38"><rect x="6" y="6" width="26" height="18" fill="none" stroke="#fff" stroke-width="3"/><path d="M19 24v8M12 32h14" stroke="#fff" stroke-width="3"/></svg></span>
      <div><h3>On-demand Training Rooms</h3><p>Flexible classroom layouts for workshops and seminars, with projectors, whiteboards and catering options for groups of any size.</p><div class="more">Read More ›</div></div>
    </div>
    <div class="service">
      <span class="service-icon"><svg width="38" height="38" viewBox="0 0 38 38"><rect x="5" y="8" width="28" height="20" rx="2" fill="none" stroke="#fff" stroke-width="3"/><path d="M14 32h10" stroke="#fff" stroke-width="3"/></svg></span>
      <div><h3>Virtual Office Solutions</h3><p>A prestigious business address, live call answering and mail handling that give your company a professional presence anywhere.</p><div class="more">Read More ›</div></div>
    </div>
  </div>
</section>

<section class="partners">
  <h2>OUR PARTNERS</h2>
  <div class="mark"></div>
  <span class="partner-arrow" style="left:16px"><svg width="12" height="18" viewBox="0 0 12 18"><path d="M10 2 3 9l7 7" stroke="#9aa0a8" stroke-width="2" fill="none"/></svg></span>
  <div class="partner-row">
    <div class="partner"><span></span></div>
    <div class="partner"><span></span></div>
    <div class="partner"><span></span></div>
    <div class="partner"><span></span></div>
    <div class="partner"><span></span></div>
    <div class="partner"><span></span></div>
  </div>
  <span class="partner-arrow" style="right:16px"><svg width="12" height="18" viewBox="0 0 12 18"><path d="m2 2 7 7-7 7" stroke="#9aa0a8" stroke-width="2" fill="none"/></svg></span>
</section>

<footer class="site-footer">
  <span class="footer-hub"></span>
  <div class="footer-cols">
    <div>
      <h4>QUICK LINKS</h4>
      <ul><li>Home</li><li>Properties</li><li>Virtual Tours &amp; Videos</li><li>Photos</li><li>Broker Referrals</li></ul>
    </div>
    <div>
      <h4>CONTACT DETAILS</h4>
      <div class="contact-line"><svg width="14" height="16" viewBox="0 0 14 16"><path d="M7 0a6 6 0 0 0-6 6c0 4.5 6 10 6 10s6-5.5 6-10a6 6 0 0 0-6-6zm0 8.5A2.5 2.5 0 1 1 7 3.5a2.5 2.5 0 0 1 0 5z" fill="#f39224"/></svg><span><b>CALLOWAY BUSINESS CENTERS</b><br>2870 Lindale Parkway<br>Suite 400, Dallas, Texas 75204</span></div>
      <div class="contact-line"><svg width="14" height="14" viewBox="0 0 24 24"><path fill="#f39224" d="M6.6 10.8a15 15 0 0 0 6.6 6.6l2.2-2.2c.3-.3.7-.4 1-.2 1.1.4 2.3.6 3.6.6.6 0 1 .4 1 1V20c0 .6-.4 1-1 1A17 17 0 0 1 3 4c0-.6.4-1 1-1h3.5c.6 0 1 .4 1 1 0 1.3.2 2.5.6 3.6.1.3 0 .7-.2 1z"/></svg><span>+214.555.0147</span></div>
      <div class="contact-line"><svg width="14" height="14" viewBox="0 0 14 14"><rect x="1" y="3" width="12" height="8" fill="none" stroke="#f39224" stroke-width="1.5"/><path d="m1 3 6 5 6-5" fill="none" stroke="#f39224" stroke-width="1.5"/></svg><span>office@callowayoffices.com</span></div>
    </div>
    <div>
      <h4>QUICK CONTACT</h4>
      <div class="form-field">Name</div>
      <div class="form-field">Email</div>
      <div class="form-field tall">Message</div>
      <span class="submit">Submit</span>
    </div>
    <div class="follow">
      <h4>FOLLOW US</h4>
      <ul><li><span class="ic"></span>CIRCLET</li><li><span class="ic"></span>CHIRPER</li><li><span class="ic"></span>LINKWORK</li><li><span class="ic"></span>PINBOARD</li></ul>
    </div>
  </div>
</footer>

<div class="copyright" style="position:absolute;left:0;width:1200px">Copyright © 2016 - Calloway Business Centers. All Rights Reserved.</div>

</body>
</html>
```